Signage Design Project

We need a logo and signage for the shopfront of a personal fitness training gym and coaching facility. We want the signage to cover the glass shopfront windows which consist of 4 glass windows with dimensions: 1 of 200cm x 180cm, 2 of 180cm x 135cm and 1 of 180cm x 180cm. The windows that are 200x 180 and 180x180 are the most visable/ important. We want the 200x180 to display the logo and our name which is "Ridgeline Fitness Centre" with further information of: Your personal training studio and boutique coaching gym Ph: 9471 2836.
For the window with 180 x 180cm measurement we want to list the services we provide which are:
Personal Training Sessions | Group Classes|Weight Loss |Toning & Sculpting|Bodybuilding I Cardio|Weights| Kettlebells| Boxing| Circuits I Team Building Programs| Boot Camp I Healthy Lifestyle & Wellness Coaching
The 2 windows 180x135cm are diagonal to the entry of the shop. We want them to be the same and plainer in design with the words: Ridgeline Fitness Centre
Personal Training Studio and Boutique Coaching Gym
The signage design also includes an acrylic window box that lights up which is to display the logo and Ridgeline Fitness Centre

```html
<!DOCTYPE html>
<html lang="en">
<head>
<meta charset="utf-8">
<title>Ridgeline Fitness Centre – Shopfront Signage</title>
<link href="https://fonts.googleapis.com/css2?family=Arimo:wght@700&family=Quicksand:wght@500;600&display=swap" rel="stylesheet">
<style>
  :root {
    --brand-blue: #0e9dbf;
    --deep-blue: #0a6f8c;
    --bright-blue: #1bb8ea;
    --text-blue: #1a9cc6;
    --lime: #a6b625;
    --white: #ffffff;
    --frame-grey: #8a8a8a;
    --photo-warm: #d9b89a;
    --photo-cool: #7fc3dc;
  }
  * { margin: 0; padding: 0; box-sizing: border-box; }
  html, body { width: 1200px; height: 900px; overflow: hidden; background: var(--white); }
  .canvas { position: relative; width: 1200px; height: 900px; }

  .brand-name {
    font-family: "Arimo", Arial, sans-serif;
    font-weight: 700;
    display: flex;
    align-items: center;
    gap: 16px;
  }
  .brand-name .brand-dot { border-radius: 50%; flex: none; }
  .brand-name .brand-words { display: flex; flex-direction: column; line-height: 1; white-space: nowrap; }

  /* Light box sign */
  .lightbox-sign {
    position: absolute; left: 319px; top: 61px; width: 563px; height: 188px;
    background: var(--brand-blue);
    display: flex; align-items: center; justify-content: center;
  }
  .lightbox-sign .brand-name { color: var(--white); }
  .lightbox-sign .brand-dot { width: 90px; height: 90px; background: var(--white); }
  .lightbox-sign .brand-main { font-size: 60px; letter-spacing: 1px; }
  .lightbox-sign .brand-sub { font-size: 28px; margin-top: 6px; letter-spacing: 1px; }

  /* Main window */
  .window-main {
    position: absolute; left: 22px; top: 292px; width: 610px; height: 546px; overflow: hidden;
  }
  .window-main .panel-bg { position: absolute; inset: 0; }
  .window-main .brand-name {
    position: absolute; left: 76px; top: 92px; color: var(--white);
  }
  .window-main .brand-dot { width: 110px; height: 110px; background: var(--white); }
  .window-main .brand-main { font-size: 60px; letter-spacing: 1px; }
  .window-main .brand-sub { font-size: 30px; margin-top: 8px; letter-spacing: 1px; }
  .tagline {
    position: absolute; left: 0; width: 610px; top: 282px;
    text-align: center; color: var(--white);
    font-family: "Quicksand", sans-serif; font-weight: 500;
    font-size: 29px; line-height: 31px; letter-spacing: 3px;
  }
  .phone {
    position: absolute; left: 0; width: 610px; top: 418px;
    display: flex; justify-content: center; align-items: center; gap: 8px;
    color: var(--white); font-family: "Quicksand", sans-serif; font-weight: 600;
    font-size: 46px; letter-spacing: 2px;
  }
  .phone .phone-icon { flex: none; }

  /* Services window */
  .window-services {
    position: absolute; left: 637px; top: 291px; width: 528px; height: 547px;
    border: 1.5px solid var(--frame-grey); overflow: hidden; background: var(--white);
  }
  .window-services .bottom-curves { position: absolute; left: 0; top: 0; }
  .window-services .brand-name {
    position: absolute; left: 94px; top: 32px; color: var(--brand-blue); gap: 14px;
  }
  .window-services .brand-dot { width: 84px; height: 84px; background: var(--brand-blue); }
  .window-services .brand-main { font-size: 46px; }
  .window-services .brand-sub { font-size: 22px; margin-top: 6px; }
  .service-list {
    position: absolute; left: 10px; right: 10px; top: 157px;
    text-align: center; color: var(--text-blue);
    font-family: "Arimo", Arial, sans-serif; font-weight: 700;
    font-size: 19.5px; line-height: 36.5px;
  }
  .service-list .sep { color: var(--lime); padding: 0 3px; }
  .athlete-photo {
    position: absolute; left: 278px; top: 336px; width: 250px; height: 200px;
    background: radial-gradient(ellipse at 45% 45%, var(--photo-warm) 0%, var(--photo-cool) 60%, rgba(127,195,220,0) 75%);
  }
</style>
</head>
<body>
<div class="canvas">

  <div class="lightbox-sign">
    <div class="brand-name">
      <span class="brand-dot"></span>
      <span class="brand-words"><span class="brand-main">RIDGELINE</span><span class="brand-sub">Fitness Centre</span></span>
    </div>
  </div>

  <section class="window-main">
    <svg class="panel-bg" width="610" height="546" viewBox="0 0 610 546">
      <defs>
        <radialGradient id="mainGlow" cx="0.5" cy="0" r="0.95">
          <stop offset="0" stop-color="#1bb8ea"/>
          <stop offset="0.55" stop-color="#0c8db3"/>
          <stop offset="1" stop-color="#0a6f8c"/>
        </radialGradient>
      </defs>
      <rect width="610" height="546" fill="url(#mainGlow)"/>
      <path d="M0,0 H240 Q40,40 0,215 Z" fill="var(--lime)"/>
      <path d="M610,325 Q600,515 380,546 H610 Z" fill="var(--lime)"/>
    </svg>
    <div class="brand-name">
      <span class="brand-dot"></span>
      <span class="brand-words"><span class="brand-main">RIDGELINE</span><span class="brand-sub">Fitness Centre</span></span>
    </div>
    <p class="tagline">Your personal training<br>studio &amp; boutique<br>coaching gym</p>
    <p class="phone">
      <svg class="phone-icon" width="26" height="42" viewBox="0 0 26 42" aria-hidden="true">
        <rect x="2" y="2" width="22" height="38" rx="4" fill="#ffffff"/>
        <rect x="6" y="7" width="14" height="12" rx="1" fill="#0a6f8c"/>
        <circle cx="13" cy="31" r="3" fill="#0a6f8c"/>
      </svg>
      <span>9471-2836</span>
    </p>
  </section>

  <section class="window-services">
    <svg class="bottom-curves" width="528" height="547" viewBox="0 0 528 547">
      <path d="M0,378 Q140,480 390,512 Q470,518 528,498 V547 H0 Z" fill="var(--lime)"/>
      <path d="M130,547 Q390,528 528,420 V547 Z" fill="var(--brand-blue)"/>
      <path d="M0,418 Q200,528 430,526" fill="none" stroke="#ffffff" stroke-width="6"/>
    </svg>
    <div class="brand-name">
      <span class="brand-dot"></span>
      <span class="brand-words"><span class="brand-main">RIDGELINE</span><span class="brand-sub">Fitness Centre</span></span>
    </div>
    <p class="service-list">
      Personal Training Sessions<span class="sep">|</span>Group Classes<br>
      Weight Loss<span class="sep">|</span>Toning &amp; Sculpting<span class="sep">|</span> Body Building<br>
      Cardio<span class="sep">|</span>Weights<span class="sep">|</span>Kettlebells<span class="sep">|</span>Boxing<span class="sep">|</span><br>
      Circuits<span class="sep">|</span>Team Building Programs<span class="sep">|</span>Boot<br>
      Camp<span class="sep">|</span>Healthy Lifestyle &amp; Wellness Coaching
    </p>
    <div class="athlete-photo" role="img" aria-label="Photo of a smiling woman in blue sportswear sitting and stretching her leg"></div>
  </section>

</div>
</body>
</html>
```